Etiketten-Design für Gin
Zielgruppe
Destillieren von GIN (BrunoLIK) / Zielgruppe alle die GIN Lieben :)
Aufgabenstellung
die Grunddatei besteht schon im AI Format, allerdings möchten wir gerne die Highlights in Kupfer haben wie Schrift und Holzfässer, gerne auch eigene Bilder entwerfen. Lediglich das BrunoLIK Logo (Kopf) sollte erhalten bleiben. Bitte die Datei so anlegen das die Highlights in Kupfer gedruckt (Siebdruck) werden können. Transparentes Etikett wäre super! Bei Fragen einfach melden :)

```html
<!DOCTYPE html>
<html lang="de">
<head>
<meta charset="utf-8">
<title>BrunoLIK Barrel Aged Gin – Etikett</title>
<link rel="stylesheet" href="https://fonts.googleapis.com/css2?family=Quicksand:wght@300;400&family=Sacramento&display=swap">
<style>
  :root {
    --page-bg: #eceeef;
    --label-core: #d3dfe1;
    --label-edge: #8f9193;
    --label-edge-soft: rgba(143, 145, 147, 0);
    --copper: #e49a78;
    --script-grey: #b0b0b2;
    --meta-grey: #dfe3e4;
  }
  html, body {
    margin: 0;
    padding: 0;
    width: 1020px;
    height: 1200px;
    overflow: hidden;
    background: var(--page-bg);
  }
  .canvas {
    position: relative;
    width: 1020px;
    height: 1200px;
  }
  .gin-label {
    position: absolute;
    left: 60px;
    top: 150px;
    width: 900px;
    height: 900px;
    overflow: hidden;
    background-color: var(--label-core);
    background-image:
      linear-gradient(to right, var(--label-edge) 0, rgba(143,145,147,0.75) 22px, rgba(143,145,147,0.25) 70px, var(--label-edge-soft) 120px),
      linear-gradient(to left, var(--label-edge) 0, rgba(143,145,147,0.75) 22px, rgba(143,145,147,0.25) 70px, var(--label-edge-soft) 120px),
      linear-gradient(to bottom, var(--label-edge) 0, rgba(143,145,147,0.5) 14px, var(--label-edge-soft) 70px),
      linear-gradient(to top, var(--label-edge) 0, rgba(143,145,147,0.55) 14px, var(--label-edge-soft) 60px);
    font-family: "Quicksand", sans-serif;
  }
  .portrait-area {
    position: absolute;
    left: 243px;
    top: 84px;
    width: 462px;
    height: 484px;
    border-radius: 46% 48% 44% 46%;
    background: radial-gradient(ellipse at 50% 50%, #dfe6e7 0%, #e8c3ad 70%, var(--copper) 100%);
    opacity: 0.85;
  }
  .product-name {
    position: absolute;
    left: 0;
    right: 0;
    top: 500px;
    margin: 0;
    text-align: center;
    font-family: "Sacramento", cursive;
    font-weight: 400;
    font-size: 250px;
    line-height: 250px;
    color: var(--script-grey);
  }
  .product-type {
    position: absolute;
    left: 0;
    right: 0;
    top: 757px;
    margin: 0;
    text-align: center;
    font-weight: 300;
    font-size: 38px;
    line-height: 46px;
    color: var(--copper);
  }
  .meta {
    position: absolute;
    top: 838px;
    margin: 0;
    font-weight: 300;
    font-size: 36px;
    line-height: 44px;
    color: var(--meta-grey);
  }
  .meta-abv { left: 40px; }
  .meta-volume { right: 40px; }
</style>
</head>
<body>
<main class="canvas">
  <section class="gin-label">
    <div class="portrait-area" role="img" aria-label="Kupferfarbene Skizze des Markenkopfes"></div>
    <h1 class="product-name">Bruno</h1>
    <p class="product-type">Barrel Aged Gin</p>
    <p class="meta meta-abv">45% vol.</p>
    <p class="meta meta-volume">0,5 l</p>
  </section>
</main>
</body>
</html>
```